Sleep/Snoring Business - Requires Website - Australia

We are seeking a simple to maintain website for our sleep business. The health care business provides diagnostic and treatment solutions for snoring, sleep disorders and other respiratory problems.

Ideally, colours to match the company logo (attached).

The page must be built using WORDPRESS.

Ideally site will have a home page outlining the business, with 5 sub pages - being "Diagnosis" "Treatment Options", "Prodcuts", "About Us", "Contact Us"

The site home page should include a large picture on the home page.

The "Treatment Options" and "Diagnosis" pages must include:
Allow for a few pictures with assocaited text, plus space for some embeded youtube videos.

"Prodcuts" page should have the ability to show 3-4 products across the page with text below.. that can include external URL to products

The "About Us" page must include:
1. a Map (google map) to identify the various locations. There are 6 in total.
2. A Section to describe our doctors/staff - allow for a picture and some text

The "Contact Us" page must include:
email form
telephone details

The overall design should have a clean and medical/safe feeling

Target Market(s)

People who snore and those with sleeping and respiratory disorders

Industry/Entity Type

Health Care

Coding

Coded - Design and coding required

Number of Pages Required

5+ page

Colors

Designer to choose colors to be used in the design.

Requirements
Must have
• The page must be built using WORDPRESS.
• Ideally site will have a home page outlining the business, with 5 sub pages - being "Diagnosis" "Treatment Options", "Prodcuts", "About Us", "Contact Us"
• The site home page should include a large picture on the home page.
• The "Treatment Options" and "Diagnosis" pages must include:
• Allow for a few pictures with assocaited text, plus space for some embeded youtube videos.
• "Prodcuts" page should have the ability to show 3-4 products across the page with text below.. that can include external URL to products
• The "About Us" page must include:
• 1. a Map (google map) to identify the various locations. There are 6 in total.
• 2. A Section to describe our doctors/staff - allow for a picture and some text
• The "Contact Us" page must include:
• email form
• telephone details
• Pictures must be licenced or free to use
Nice to have
• Home page pictures showing people sleeping well, snoring or fresh air (landscape) type transition pictures (at least 3).
Should not have
• Not to look cheap
• This is a high end healthcare business, so must look that way

```html
<!DOCTYPE html>
<html lang="en">
<head>
<meta charset="utf-8">
<title>Restwell – Diagnostic and Treatment Solutions for Snoring</title>
<link rel="stylesheet" href="https://fonts.googleapis.com/css2?family=Montserrat:wght@600;700&family=Nunito+Sans:wght@300;400;600&family=Open+Sans:wght@400;600&display=swap">
<style>
:root{
  --navy:#163f7a;
  --navy-deep:#1d3d78;
  --ink:#555b63;
  --muted:#7d8590;
  --nav:#6f7680;
  --white:#ffffff;
  --band-blue:#0e3f9a;
  --news-bg:#a9b9dc;
  --news-sub:#d9e1f1;
  --rule:#d8dbe0;
}
*{margin:0;padding:0;box-sizing:border-box}
html,body{width:1200px;height:2347px;overflow:hidden;background:var(--white)}
body{position:relative;font-family:"Open Sans",Arial,sans-serif;color:var(--ink)}
.abs{position:absolute}

/* header */
.site-header{position:absolute;left:0;top:0;width:1200px;height:106px;background:var(--white)}
.brand{position:absolute;left:125px;top:30px;font-family:"Nunito Sans",Arial,sans-serif;font-weight:600;font-size:40px;color:var(--navy);letter-spacing:.5px;display:flex;align-items:center;gap:10px}
.brand-dot{width:12px;height:12px;border-radius:50%;background:var(--navy);flex:none}
.main-nav a{position:absolute;top:48px;font-family:"Nunito Sans",Arial,sans-serif;font-size:17px;color:var(--nav);text-decoration:none;letter-spacing:.3px}
.main-nav a.active{color:var(--navy)}
.nav-underline{position:absolute;left:460px;top:101px;width:67px;height:3px;background:var(--navy)}

/* hero */
.hero{position:absolute;left:0;top:106px;width:1200px;height:551px;background:linear-gradient(100deg,#9fb0c6 0%,#6f7f95 45%,#8a97a8 70%,#c3ccd6 100%)}
.hero-title{position:absolute;left:0;top:0;width:1200px;text-align:center;color:var(--white);font-family:"Montserrat",Arial,sans-serif}
.hero-title .l1{position:absolute;left:0;width:1200px;top:310px;font-size:41px;line-height:50px;font-weight:700;letter-spacing:1px}
.hero-title .l2{position:absolute;left:0;width:1200px;top:358px;font-size:31px;line-height:40px;font-weight:600;letter-spacing:1px}
.slider-dots{position:absolute;left:535px;top:621px;display:flex;gap:8px}
.slider-dots span{width:27px;height:3px;background:var(--white)}

/* about + video */
.section-title{font-family:"Nunito Sans",Arial,sans-serif;font-weight:300;font-size:31px;color:#4a5058}
.about-title{left:130px;top:714px}
.diag-title{left:605px;top:714px;color:var(--navy);font-weight:400}
.about-copy{left:130px;top:772px;font-size:13px;line-height:23.5px;color:var(--ink);white-space:nowrap}
.about-copy p+p{margin-top:10px}
.btn-outline{position:absolute;display:flex;align-items:center;justify-content:center;border:2px solid var(--navy);color:var(--navy);font-family:"Nunito Sans",Arial,sans-serif;font-size:14px;letter-spacing:.5px;text-decoration:none}
.btn-about{left:135px;top:1012px;width:139px;height:41px}
.video-frame{left:607px;top:770px;width:462px;height:284px;background:linear-gradient(135deg,#b9b2a6 0%,#8c8f93 45%,#5e6a78 100%)}
.play{position:absolute;left:801px;top:876px}

/* treatment band */
.treatment{position:absolute;left:0;top:1153px;width:1200px;height:407px;background:radial-gradient(ellipse at 70% 40%,#2a63c4 0%,var(--band-blue) 55%,#0a2c6e 100%)}
.treatment-title{position:absolute;left:0;width:1200px;top:1234px;text-align:center;font-family:"Nunito Sans",Arial,sans-serif;font-weight:300;font-size:35px;color:var(--white)}
.treatment-copy{position:absolute;left:200px;top:1302px;width:800px;text-align:center;font-size:13.5px;line-height:23.5px;color:var(--white);white-space:nowrap}
.treatment-copy p+p{margin-top:12px}
.btn-light{left:529px;top:1438px;width:136px;height:40px;border-color:var(--white);color:var(--white)}

/* news */
.news{position:absolute;left:0;top:1560px;width:1200px;height:414px;background:var(--news-bg)}
.news-title{position:absolute;left:133px;top:1626px;font-family:"Nunito Sans",Arial,sans-serif;font-weight:300;font-size:31px;color:var(--white)}
.news-card .thumb{position:absolute;top:1701px;width:174px;height:178px}
.news-card h3{position:absolute;top:1693px;font-family:"Nunito Sans",Arial,sans-serif;font-weight:600;font-size:18px;line-height:26px;color:var(--white);white-space:nowrap}
.news-card p{position:absolute;top:1781px;font-size:13.5px;line-height:22px;color:var(--news-sub);white-space:nowrap}
.btn-solid{position:absolute;top:1841px;width:127px;height:38px;background:var(--navy-deep);color:var(--white);display:flex;align-items:center;justify-content:center;font-family:"Nunito Sans",Arial,sans-serif;font-size:15px;text-decoration:none}

/* footer */
.footer-brand{position:absolute;left:149px;top:2082px;font-family:"Nunito Sans",Arial,sans-serif;font-weight:600;font-size:46px;line-height:56px;color:var(--navy);display:flex;align-items:center;gap:10px}
.footer-brand .brand-dot{width:13px;height:13px}
.footer-col h4{position:absolute;top:2045px;font-family:"Nunito Sans",Arial,sans-serif;font-weight:400;font-size:21px;color:var(--navy);letter-spacing:.3px}
.footer-col ul{position:absolute;top:2089px;list-style:none}
.footer-col li{font-size:14px;line-height:28px;color:var(--ink);white-space:nowrap}
.social{position:absolute;left:629px;top:2183px;display:flex;gap:7px}
.social span{width:28px;height:28px;border:1.5px solid #a9b3c6;border-radius:50%}
.footer-rule{position:absolute;left:141px;top:2276px;width:931px;height:1px;background:var(--rule)}
.copyright{position:absolute;left:0;width:1200px;top:2300px;text-align:center;font-size:12px;color:var(--muted)}
</style>
</head>
<body>

<header class="site-header">
  <div class="brand"><span>Restwell</span><span class="brand-dot"></span></div>
  <nav class="main-nav">
    <a class="active" href="#" style="left:468px">HOME</a>
    <a href="#" style="left:544px">DIAGNOSIS</a>
    <a href="#" style="left:663px">TREATMENT OPTIONS</a>
    <a href="#" style="left:867px">ABOUT US</a>
    <a href="#" style="left:976px">CONTACT US</a>
  </nav>
  <div class="nav-underline"></div>
</header>

<section class="hero" role="img" aria-label="Photo of a tired man sitting cross-legged on an unmade bed in a softly lit bedroom"></section>
<div class="hero-title">
  <div class="l1">DIAGNOSTIC AND TREATMENT</div>
  <div class="l2">SOLUTIONS FOR SNORING</div>
</div>
<div class="slider-dots"><span></span><span></span><span></span><span></span></div>

<h2 class="abs section-title about-title">About Sleep</h2>
<div class="abs about-copy">
  <p>Praesent elementum elit at tellus nec ultricies sit amet porttitor<br>mattis enim In massa libero interdum nec interdum vel blandit sed<br>nulla In ullamcorper est eget tempor cursus neque mi<br>consectetuer mi a ultricies massa</p>
  <p>est sed nisl Class aptent taciti sociosqu ad litora torquent per<br>conubia nostra per inceptos hymenaeos Proin nulla arcu<br>nonummy luctus dictum eget&nbsp; Class aptent taciti sociosqu ad litora<br>torquent per conubia nostra per inceptos hymenaeos Proin nulla<br>arcu nonummy luctus dictum eget fermentum et lorem</p>
</div>
<a class="btn-outline btn-about" href="#">READ MORE</a>

<h2 class="abs section-title diag-title">Diagnostic Techniques</h2>
<div class="abs video-frame" role="img" aria-label="Video still of a patient lying on a clinic bed beside sleep diagnostic equipment"></div>
<svg class="play" width="72" height="72" viewBox="0 0 72 72" aria-hidden="true">
  <circle cx="36" cy="36" r="34" fill="none" stroke="#ffffff" stroke-width="2.5"/>
  <path d="M29 24 L50 36 L29 48 Z" fill="none" stroke="#ffffff" stroke-width="2.5" stroke-linejoin="round"/>
</svg>

<section class="treatment" role="img" aria-label="Deep blue background image of a DNA double helix"></section>
<h2 class="treatment-title">Treatment Options</h2>
<div class="treatment-copy">
  <p>Praesent elementum elit at tellus nec ultricies sit amet porttitor mattis enim In massa libero interdum nec<br>interdum vel blandit sed nulla In ullamcorper est eget tempor cursus neque mi consectetuer mi a ultricies massa</p>
  <p>est sed nisl Class aptent taciti sociosqu ad litora torquent per conubia nostra per inceptos hymenaeos Proin nulla<br>arcu nonummy luctus dictum eget</p>
</div>
<a class="btn-outline btn-light" href="#">READ MORE</a>

<section class="news"></section>
<h2 class="news-title">Latest News &amp; Blogs</h2>

<article class="news-card">
  <div class="thumb" style="left:128px;background:linear-gradient(135deg,#f1ece6 0%,#d9cfc6 60%,#e9e3dc 100%)" role="img" aria-label="Photo of a woman kept awake by a partner snoring beside her"></div>
  <h3 style="left:314px">Curabitur vel mi sit amet magna<br>malesuada ultrices Ut nisi erat<br>fermentum</h3>
  <p style="left:314px">Etiam est nunc venenatis in tristique eu<br>imperdiet ac nisl Cum sociis natoque</p>
  <a class="btn-solid" href="#" style="left:319px">Read More</a>
</article>

<article class="news-card">
  <div class="thumb" style="left:616px;background:linear-gradient(135deg,#e4e8ee 0%,#a9b3c2 55%,#dfe3ea 100%)" role="img" aria-label="Photo of a man sleeping on his side wearing a CPAP mask"></div>
  <h3 style="left:801px">Curabitur vel mi sit amet magna<br>malesuada ultrices Ut nisi erat<br>fermentum</h3>
  <p style="left:801px">Etiam est nunc venenatis in tristique eu<br>imperdiet ac nisl Cum sociis natoque</p>
  <a class="btn-solid" href="#" style="left:807px">Read More</a>
</article>

<footer>
  <div class="footer-brand"><span>Restwell</span><span class="brand-dot"></span></div>

  <div class="footer-col">
    <h4 style="left:433px">QUICK LINKS</h4>
    <ul style="left:433px"><li>Home</li><li>Diagnosis</li><li>Treatment Options</li><li>About us</li></ul>
  </div>
  <div class="footer-col">
    <h4 style="left:630px">RESOURCES</h4>
    <ul style="left:630px"><li>Contact Us</li><li>Privacy Policy</li><li>Term of Use</li></ul>
  </div>
  <div class="social" aria-label="Social links"><span></span><span></span><span></span><span></span></div>
  <div class="footer-col">
    <h4 style="left:829px">CONTACT US</h4>
    <ul style="left:834px"><li>214 Harbour Crest Road Suite 12</li><li>Northgate, NSW 2150</li><li>(02) 5550 1843</li><li>hello@restwellclinic.example</li></ul>
  </div>

  <div class="footer-rule"></div>
  <div class="copyright">© 2017 Company Name&nbsp; All right reserved&nbsp; Term of Use</div>
</footer>

</body>
</html>
```